Corporate Business Card

Very professional, Modern, Not to busy, include phone address email, website
(253) 617-4930, 18761 52nd Avenue S, Kent, WA 98047, martin@plumlinegroup.com, varkoworks.com

Target Market(s)

Manufacturing

Industry/Entity Type

Aero, machining, manufacturing, Off road racing

Contact Information for Business Card

Phone, address email, website

```html
<!DOCTYPE html>
<html lang="en">
<head>
<meta charset="utf-8">
<title>Varko Works – Business Card</title>
<link href="https://fonts.googleapis.com/css2?family=Montserrat:wght@400;500;700;800&display=swap" rel="stylesheet">
<style>
  :root {
    --stage: #2b2b2d;
    --card: #141416;
    --blue: #1f3f8f;
    --red: #d8232a;
    --white: #f2f2f2;
  }
  * { box-sizing: border-box; margin: 0; padding: 0; }
  html, body { width: 1200px; height: 839px; overflow: hidden; }
  body {
    background: var(--stage);
    font-family: "Montserrat", sans-serif;
    position: relative;
  }
  .card {
    position: absolute;
    top: 70px;
    width: 400px;
    height: 700px;
    background: var(--card);
    border-radius: 26px;
  }
  .card-front { left: 170px; }
  .card-back { left: 630px; }

  /* front */
  .brand {
    position: absolute;
    top: 92px;
    left: 0; right: 0;
    text-align: center;
    color: var(--blue);
    font-weight: 800;
    font-size: 46px;
    letter-spacing: 1px;
    text-transform: uppercase;
  }
  .brand-rule {
    position: absolute;
    top: 170px;
    left: 60px;
    width: 280px;
    height: 3px;
    background: var(--blue);
  }
  .person {
    position: absolute;
    top: 206px;
    left: 0; right: 0;
    text-align: center;
  }
  .person-name {
    color: var(--blue);
    font-weight: 700;
    font-size: 25px;
    letter-spacing: 1px;
  }
  .person-role {
    color: var(--white);
    font-size: 15px;
    margin-top: 6px;
    letter-spacing: .5px;
  }
  .divider {
    position: absolute;
    left: 30px; right: 30px;
    display: flex;
    align-items: center;
    justify-content: center;
    gap: 10px;
  }
  .divider .line { flex: 1; height: 2px; background: var(--blue); }
  .divider .stars { color: var(--blue); font-size: 11px; letter-spacing: 2px; white-space: nowrap; }
  .divider .stars .big { font-size: 17px; }
  .divider-contact { top: 330px; }
  .divider-address { top: 520px; }
  .icon {
    width: 28px; height: 28px;
    background: var(--blue);
    display: flex; align-items: center; justify-content: center;
  }
  .icon svg { width: 17px; height: 17px; }
  .contact {
    position: absolute;
    top: 395px;
    left: 0; right: 0;
    text-align: center;
    color: var(--white);
    font-size: 16px;
    line-height: 27px;
    letter-spacing: .3px;
  }
  .address {
    position: absolute;
    top: 580px;
    left: 0; right: 0;
    text-align: center;
    color: var(--white);
    font-size: 17px;
    line-height: 28px;
    letter-spacing: .5px;
  }

  /* back */
  .back-rule {
    position: absolute;
    top: 250px;
    bottom: 60px;
    left: 118px;
    width: 3px;
    background: var(--blue);
  }
  .back-brand {
    position: absolute;
    top: 70px;
    left: 170px;
    writing-mode: vertical-rl;
    color: var(--blue);
    font-weight: 800;
    font-size: 96px;
    letter-spacing: 4px;
    text-transform: uppercase;
    line-height: 1;
  }
</style>
</head>
<body>

<section class="card card-front">
  <div class="brand">Varko Works</div>
  <div class="brand-rule"></div>

  <div class="person">
    <div class="person-name">DANIEL MERCER</div>
    <div class="person-role">Owner/CEO</div>
  </div>

  <div class="divider divider-contact">
    <span class="line"></span>
    <span class="stars">★★<span class="big">★</span></span>
    <span class="icon" aria-label="Phone">
      <svg viewBox="0 0 24 24" fill="#fff"><path d="M6.6 10.8a15.1 15.1 0 0 0 6.6 6.6l2.2-2.2a1 1 0 0 1 1-.25 11.4 11.4 0 0 0 3.6.57 1 1 0 0 1 1 1V20a1 1 0 0 1-1 1A17 17 0 0 1 3 4a1 1 0 0 1 1-1h3.5a1 1 0 0 1 1 1c0 1.25.2 2.45.57 3.57a1 1 0 0 1-.25 1z"/></svg>
    </span>
    <span class="icon" aria-label="Email">
      <svg viewBox="0 0 24 24" fill="#fff"><path d="M3 6h18v12H3z"/><path d="M3 6l9 7 9-7" fill="none" stroke="#1f3f8f" stroke-width="2"/></svg>
    </span>
    <span class="icon" aria-label="Website">
      <svg viewBox="0 0 24 24" fill="none" stroke="#fff" stroke-width="2"><circle cx="12" cy="12" r="9"/><path d="M3 12h18M12 3c3 3.5 3 14.5 0 18M12 3c-3 3.5-3 14.5 0 18"/></svg>
    </span>
    <span class="stars"><span class="big">★</span>★★</span>
    <span class="line"></span>
  </div>

  <div class="contact">
    <div>(253) 617-4930</div>
    <div>martin@plumlinegroup.com</div>
    <div>www.varkoworks.com</div>
  </div>

  <div class="divider divider-address">
    <span class="line"></span>
    <span class="stars">★★<span class="big">★</span></span>
    <span class="icon" aria-label="Location">
      <svg viewBox="0 0 24 24" fill="#fff"><path d="M12 2a7 7 0 0 0-7 7c0 5 7 13 7 13s7-8 7-13a7 7 0 0 0-7-7zm0 9.5A2.5 2.5 0 1 1 12 6.5a2.5 2.5 0 0 1 0 5z"/></svg>
    </span>
    <span class="stars"><span class="big">★</span>★★</span>
    <span class="line"></span>
  </div>

  <div class="address">
    <div>1140, 18761 52nd Avenue</div>
    <div>S, Kent, WA 98047</div>
  </div>
</section>

<section class="card card-back">
  <div class="back-rule"></div>
  <div class="back-brand">Varko Works</div>
</section>

</body>
</html>
```